real esate business card with company logo and name

we need a business card design for a real esate company

The company name is Walsh & Brand Pty Ltd, and we have our logo designed and will upload. We want classic or moden feel. Black or white background. looks more textured. Should include folowinginformations
Owen Walsh and Lucy Brand
Sales Agents & Onsite Manager
p: 07 5948 2063
F: 07 5948 2174
M:0431 857 219
3/42 Marlow Crescent, FERNLEA QLD 4213

We want this business card looks professonal. Thank you in advance.

Industry/Entity Type

Real Estate Agent

Contact Information for Business Card

Owen Walsh and Lucy Brand
Onsite Manager & Sales Agents
p: 07 5948 2063
M:0431 857 219

Font styles to use
Serif

Colors
000000
fbfbfb
333333
959595

Requirements
Must have
• company logo and name, black or white back ground

```html
<!DOCTYPE html>
<html lang="en">
<head>
<meta charset="utf-8">
<title>Walsh &amp; Brand Pty Ltd — Business Card</title>
<link href="https://fonts.googleapis.com/css2?family=Tinos:ital,wght@0,400;0,700;1,400&display=swap" rel="stylesheet">
<style>
  :root {
    --backdrop: #eeeeee;
    --card: #fbfbfb;
    --ink-strong: #333333;
    --ink: #444444;
    --ink-soft: #959595;
    --mark: #8a8a8a;
  }
  * { margin: 0; padding: 0; box-sizing: border-box; }
  html, body {
    width: 1200px;
    height: 1200px;
    overflow: hidden;
    background: var(--backdrop);
    font-family: "Tinos", "Times New Roman", serif;
  }
  .canvas {
    width: 1200px;
    height: 1200px;
    display: flex;
    align-items: center;
    justify-content: center;
  }
  .business-card {
    width: 500px;
    height: 860px;
    background: var(--card);
    box-shadow: 0 18px 40px rgba(0,0,0,0.12), 0 2px 6px rgba(0,0,0,0.08);
    display: flex;
    flex-direction: column;
    align-items: center;
    padding-top: 150px;
  }
  .brand {
    display: flex;
    flex-direction: column;
    align-items: center;
    gap: 22px;
  }
  .brand-square {
    width: 96px;
    height: 96px;
    background: var(--mark);
  }
  .brand-name {
    font-size: 21px;
    font-weight: 400;
    letter-spacing: 0.5px;
    color: var(--ink-soft);
    text-transform: uppercase;
  }
  .agents {
    margin-top: 88px;
    text-align: center;
  }
  .agent-names {
    font-size: 25px;
    font-weight: 700;
    color: var(--ink-strong);
    text-transform: uppercase;
    letter-spacing: 0.2px;
  }
  .agent-role {
    margin-top: 14px;
    font-size: 23px;
    font-style: italic;
    color: var(--ink);
  }
  .contact {
    margin-top: 70px;
    align-self: flex-start;
    margin-left: 120px;
    list-style: none;
    font-size: 21px;
    line-height: 1.55;
    color: var(--ink-strong);
  }
</style>
</head>
<body>
  <main class="canvas">
    <article class="business-card">
      <header class="brand">
        <div class="brand-square"></div>
        <div class="brand-name">Walsh &amp; Brand Pty Ltd.</div>
      </header>
      <section class="agents">
        <h1 class="agent-names">Owen Walsh and Lucy Brand</h1>
        <p class="agent-role">Onsite Manager &amp; Sales Agents</p>
      </section>
      <ul class="contact">
        <li>p: 07 5948 2063</li>
        <li>M:0431 857 219</li>
        <li>3/42 Marlow Crescent,</li>
        <li>FERNLEA QLD 4213</li>
      </ul>
    </article>
  </main>
</body>
</html>
```